KTWG application splash screen

We need a 1024x768 image for use as an application splash screen.
The image will be displayed full screen on an 10 inch industrial PC 1024x768 screen while our application is launching. The image should convey that the application is "Waiting for connection to Wi-Fi access point..." and include a graphic of the industrial PC connected to the access point via an Ethernet cable. A list of troubleshooting steps should be included at the bottom of the image. The troubleshooting steps should not be the main focus of the image and should be shown in a smaller font (but still readable at 1024x768 displayed on a 10 inch screen).
I will include a mock up of the general idea of what we are looking for as well as image files for the industrial PC, a screenshot of our application to show on the PC's screen and the AP.
For general look and feel and a sense of corporate branding please review our website https://marrowgatesoilworks.example/. The splash screen should reflect corporate branding.
Target Market(s)
Users of our application
Industry/Entity Type
Agriculture
Look and feel

```html
<!DOCTYPE html>
<html lang="en">
<head>
<meta charset="utf-8">
<title>KTWG – Waiting for Wi-Fi access point</title>
<link href="https://fonts.googleapis.com/css2?family=Poppins:wght@400;600;700&family=Roboto:wght@700&display=swap" rel="stylesheet">
<style>
  :root{
    --stage:#333333;
    --paper-light:#ffffff;
    --paper-mid:#ececec;
    --paper-dark:#d3d3d3;
    --ink:#1e1e1e;
    --ink-soft:#454545;
    --green:#2dbb6a;
    --device-dark:#2a2a2a;
    --ap-white:#f2f2f2;
  }
  *{margin:0;padding:0;box-sizing:border-box}
  html,body{width:1200px;height:1045px;overflow:hidden;background:var(--stage)}
  .splash{
    position:absolute;left:0;top:72px;width:1200px;height:900px;
    background:linear-gradient(100deg,var(--paper-light) 0%,var(--paper-mid) 55%,var(--paper-dark) 100%);
    font-family:"Poppins",sans-serif;color:var(--ink);overflow:hidden;
  }
  .wifi-icon{position:absolute;left:558px;top:74px;width:96px;height:70px}
  .headline{
    position:absolute;left:0;top:150px;width:1200px;text-align:center;
    font-size:39px;font-weight:400;line-height:50px;letter-spacing:.5px;
  }
  .device{position:absolute;border-radius:16px}
  .device--pc{left:125px;top:298px;width:343px;height:272px;background:linear-gradient(180deg,#3a3a3a,var(--device-dark))}
  .device--ap{left:1054px;top:290px;width:28px;height:226px;border-radius:8px;
    background:linear-gradient(90deg,#dcdcdc,var(--ap-white),#d8d8d8)}
  .cable{position:absolute;left:0;top:0;width:1200px;height:900px;pointer-events:none}
  .label{position:absolute;font-family:"Roboto",sans-serif;font-weight:700;font-size:19px;letter-spacing:.2px;color:var(--ink)}
  .label--pc{left:165px;top:586px}
  .label--cable{left:511px;top:553px}
  .label--ap{left:886px;top:553px}
  .troubleshoot{position:absolute;left:126px;top:648px;width:1000px}
  .troubleshoot__title{display:flex;align-items:center;gap:8px;color:var(--green);font-weight:600;font-size:20px}
  .troubleshoot__title svg{width:30px;height:30px}
  .steps{list-style:none;margin:6px 0 0 36px;font-size:15px;color:var(--ink-soft);line-height:25px}
  .steps li{position:relative;padding-left:20px}
  .steps li::before{content:"";position:absolute;left:0;top:8px;width:10px;height:10px;border-radius:50%;background:var(--ink)}
  .steps .steps{margin:2px 0 0 15px}
  .brand{position:absolute;left:996px;top:796px;font-weight:700;font-size:30px;letter-spacing:1px;color:var(--ink-soft)}
</style>
</head>
<body>
<main class="splash">
  <svg class="wifi-icon" viewBox="0 0 96 70" aria-hidden="true">
    <path d="M4 24 A62 62 0 0 1 92 24 L82 34 A48 48 0 0 0 14 34 Z" fill="var(--green)"/>
    <path d="M22 42 A37 37 0 0 1 74 42 L64 52 A23 23 0 0 0 32 52 Z" fill="var(--green)"/>
    <path d="M38 58 L48 48 L58 58 L48 68 Z" fill="var(--green)"/>
  </svg>

  <h1 class="headline">Waiting for connection to<br>Wi-Fi access point...</h1>

  <div class="device device--pc" role="img" aria-label="Rugged tractor cab computer showing the planter monitoring app with green row bars"></div>

  <svg class="cable" viewBox="0 0 1200 900" aria-hidden="true">
    <rect x="468" y="524" width="20" height="22" rx="3" fill="#1a1a1a"/>
    <path d="M488 535 H1058 Q1068 535 1068 525 V514" fill="none" stroke="#1a1a1a" stroke-width="3"/>
  </svg>

  <div class="device device--ap" role="img" aria-label="White outdoor Wi-Fi access point with two antennas and a green status light"></div>

  <div class="label label--pc">TRACTOR CAB COMPUTER</div>
  <div class="label label--cable">ETHERNET CABLE</div>
  <div class="label label--ap">WI-FI ACCESS POINT</div>

  <section class="troubleshoot">
    <h2 class="troubleshoot__title">
      <svg viewBox="0 0 30 30" aria-hidden="true"><circle cx="15" cy="15" r="9" fill="none" stroke="var(--green)" stroke-width="2" stroke-dasharray="4 2.5"/><circle cx="15" cy="15" r="4" fill="none" stroke="var(--green)" stroke-width="2"/><path d="M4 26 L11 19" stroke="var(--green)" stroke-width="2.5" stroke-linecap="round"/></svg>
      Troubleshooting steps:
    </h2>
    <ul class="steps">
      <li>This screen should only be visible for a short time on boot.</li>
      <li>If this screen stays visible for more than a minute:
        <ul class="steps">
          <li>Verify that the Wi-Fi Access Point (AP) powers up when this system does (indicated by a green light on the side of the AP).</li>
          <li>Check the Ethernet cable between this system and the AP for damage, and replace it if necessary.</li>
          <li>Power-cycle this system and wait for it to reboot fully.</li>
          <li>If the issue persists, contact KTWG support for further assistance.</li>
        </ul>
      </li>
    </ul>
  </section>

  <div class="brand">KTWG</div>
</main>
</body>
</html>
```